Unique Business Card Design

Unique Business Card design for our orthotic and prosthetic company. Our logo is on our website, color is light blue. Unique shape (artificial leg shaped, vertical, etc..) preferred. Logo, business name, individual name and basic demographics needed.

Industry/Entity Type

Business

Contact Information for Business Card

Logo, Industry, Phone # Logo, "Prosthetic & Orthotic Services" Place to add individual name and contact info

Colors
cee9f5

Requirements
Must have
• The icon must be there, placement of "Prosthetic & Orthotic Services" can be moved
Nice to have
• Like the mix of light blue, and a little darker blue. One design included the icons from my website which was a nice touch

```html
<!DOCTYPE html>
<html lang="en">
<head>
<meta charset="utf-8">
<title>Limbwell Inc. Business Card</title>
<link rel="stylesheet" href="https://fonts.googleapis.com/css2?family=Open+Sans:wght@400;600&family=Roboto:wght@400;700&family=EB+Garamond:ital@1&display=swap">
<style>
  :root {
    --brand-blue: #22619b;
    --brand-blue-deep: #1d5589;
    --stripe-grey: #3a3f45;
    --card-white: #f4f4f4;
    --ink: #2b2b2b;
    --page: #e8e8e9;
    --white: #ffffff;
  }
  * { margin: 0; padding: 0; box-sizing: border-box; }
  html, body { width: 1200px; height: 576px; overflow: hidden; background: var(--page); }
  .canvas { position: relative; width: 1200px; height: 576px; }

  .card {
    position: absolute;
    border-radius: 6px;
    overflow: hidden;
    box-shadow: 0 3px 6px rgba(0,0,0,0.22);
  }

  /* Front */
  .card-front {
    left: 82px; top: 139px; width: 485px; height: 292px;
    background: linear-gradient(180deg, var(--brand-blue), var(--brand-blue-deep));
    color: var(--white);
  }
  .front-mark {
    position: absolute; left: 91px; top: 106px;
    width: 78px; height: 78px; border-radius: 50%; background: var(--white);
  }
  .front-name {
    position: absolute; left: 190px; top: 98px;
    font: 600 21px/1 "Open Sans", sans-serif; letter-spacing: 0.2px;
  }
  .front-rule {
    position: absolute; left: 190px; top: 137px; width: 202px; height: 2px; background: var(--white);
  }
  .front-tagline {
    position: absolute; left: 190px; top: 140px; width: 202px; text-align: center;
    font: italic 14px/1.2 "EB Garamond", serif;
  }
  .front-phone {
    position: absolute; left: 190px; top: 156px; width: 202px; text-align: center;
    font: 600 22px/1 "Open Sans", sans-serif; letter-spacing: 1px;
  }

  /* Back */
  .card-back {
    left: 602px; top: 138px; width: 480px; height: 291px;
    background: var(--card-white);
  }
  .back-shape { position: absolute; inset: 0; }
  .back-mark {
    position: absolute; left: 65px; top: 83px;
    width: 80px; height: 80px; border-radius: 50%; background: var(--white);
  }
  .back-name {
    position: absolute; left: 0; top: 168px; width: 210px; text-align: center;
    font: 600 18px/1 "Open Sans", sans-serif; color: var(--white);
  }
  .back-rule {
    position: absolute; left: 27px; top: 190px; width: 157px; height: 2px; background: var(--white);
  }
  .back-tagline {
    position: absolute; left: 0; top: 193px; width: 210px; text-align: center;
    font: italic 11px/1.2 "EB Garamond", serif; color: var(--white);
  }

  .person { position: absolute; left: 248px; top: 52px; font-family: "Roboto", sans-serif; }
  .person-name { font-weight: 700; font-size: 20px; color: var(--brand-blue); line-height: 1; }
  .person-title { margin-top: 6px; font-style: italic; font-size: 11.5px; color: var(--ink); }
  .contact-list { position: absolute; left: 248px; list-style: none; font: 400 12.5px/1 "Roboto", sans-serif; color: var(--ink); }
  .contact-mobile { top: 96px; font-size: 14px; }
  .contact-office { top: 143px; }
  .contact-list li { display: flex; align-items: center; height: 17.5px; }
  .contact-list svg { width: 11px; height: 11px; margin-right: 12px; fill: var(--brand-blue); flex: none; }
  .contact-mobile svg { height: 14px; }
  .address { position: absolute; left: 248px; top: 220px; font: 400 12.5px/1 "Roboto", sans-serif; color: var(--ink); }
</style>
</head>
<body>
<main class="canvas">
  <section class="card card-front">
    <div class="front-mark"></div>
    <div class="front-name">LIMBWELL INC.</div>
    <div class="front-rule"></div>
    <div class="front-tagline">Prosthetic &amp; Orthotic Services</div>
    <div class="front-phone">718.555.0140</div>
  </section>

  <section class="card card-back">
    <svg class="back-shape" viewBox="0 0 480 291" preserveAspectRatio="none">
      <path d="M0 0 H196 C230 40 236 90 232 140 C229 190 220 245 212 291 H0 Z" fill="var(--stripe-grey)"/>
      <path d="M0 0 H178 C212 40 220 90 216 140 C213 190 204 245 196 291 H0 Z" fill="var(--brand-blue)"/>
    </svg>
    <div class="back-mark"></div>
    <div class="back-name">LIMBWELL INC.</div>
    <div class="back-rule"></div>
    <div class="back-tagline">Prosthetic &amp; Orthotic Services</div>

    <div class="person">
      <div class="person-name">Talia Brennan</div>
      <div class="person-title">Orthotist/Prosthetist</div>
    </div>
    <ul class="contact-list contact-mobile">
      <li><svg viewBox="0 0 10 14"><path d="M1.5 0h7A1.5 1.5 0 0 1 10 1.5v11A1.5 1.5 0 0 1 8.5 14h-7A1.5 1.5 0 0 1 0 12.5v-11A1.5 1.5 0 0 1 1.5 0zM2 2v8.5h6V2zm3 9.3a.9.9 0 1 0 0 1.8.9.9 0 0 0 0-1.8z"/></svg>845-5550192</li>
    </ul>
    <ul class="contact-list contact-office">
      <li><svg viewBox="0 0 12 12"><path d="M1 4C1 2 3 1 6 1s5 1 5 3v1H8.5V3.8h-5V5H1zM3 6h6l2 2v3H1V8zm3 1.2A1.3 1.3 0 1 0 6 9.8 1.3 1.3 0 0 0 6 7.2z"/></svg>718.555.0140</li>
      <li><svg viewBox="0 0 12 12"><path d="M3 0h6v3H3zM1 4h10a1 1 0 0 1 1 1v4H9.5v3h-7V9H0V5a1 1 0 0 1 1-1zm2.5 4v3h5V8z"/></svg>718.555.0147</li>
      <li><svg viewBox="0 0 12 12"><path d="M6 0a6 6 0 1 0 0 12A6 6 0 0 0 6 0zm4.8 5.4H8.9A9 9 0 0 0 8 1.6a4.9 4.9 0 0 1 2.8 3.8zM6 1.1c.7.8 1.4 2.3 1.6 4.3H4.4C4.6 3.4 5.3 1.9 6 1.1zM4 1.6a9 9 0 0 0-.9 3.8H1.2A4.9 4.9 0 0 1 4 1.6zM1.2 6.6h1.9A9 9 0 0 0 4 10.4a4.9 4.9 0 0 1-2.8-3.8zM6 10.9c-.7-.8-1.4-2.3-1.6-4.3h3.2c-.2 2-.9 3.5-1.6 4.3zm2 -.5a9 9 0 0 0 .9-3.8h1.9A4.9 4.9 0 0 1 8 10.4z"/></svg>www.limbwellinc.com</li>
      <li><svg viewBox="0 0 12 12"><path d="M0 2h12v1L6 7 0 3zm0 2.3 6 4 6-4V10H0z"/></svg>Tbrennan@limbwellinc.com</li>
    </ul>
    <div class="address">2150 Ocean Ave. Brooklyn, NY 11229</div>
  </section>
</main>
</body>
</html>
```